Computer Company needs a Business card design

We need a business card design for our business. We assist people to transition to the KVS (Kestrel Vantage Scheme). The Verandal Crown Office-owned kvs™ network is a brand new telecommunications network currently being rolled out across Australia, giving access to a reliable broadband connection. Our niche market will predominantly be domestic customers in the 50+ age bracket. The assistance that we provide is everything from arranging the equipment, arranging the plan and contract term, appointment times, final testing of the network and any tweaks that need to be made. We basically PM the transition from start to finish. The business card design should be minimalist, should communicate loyalty and stability, should be easy to read and clearly explain what we do. We have asked for front and back. However, the back of the card does not have to include much information at all. It could be just a small design, or a repeat of our phone number. Up to you. The attached file only says what is required on the card. It does not specify where to arrange the text, what fonts to use, etc etc. As much as we would like to give you more info, due to our very limited design ability, we are not really able to send you any rough, or otherwise, designs of what we are after. Hopefully the above description is enough for you.

```html
<!DOCTYPE html>
<html lang="en">
<head>
<meta charset="utf-8">
<title>Linkway Assist – Business Card</title>
<link rel="stylesheet" href="https://fonts.googleapis.com/css2?family=Open+Sans:wght@300;400;600;700&display=swap">
<style>
  :root {
    --backdrop: #a3a3a3;
    --card-blue: #0a84ac;
    --card-white: #f4f4f4;
    --ink-white: #ffffff;
    --brand-blue: #0a84ac;
    --card-shadow: rgba(0, 0, 0, 0.28);
  }
  * { margin: 0; padding: 0; box-sizing: border-box; }
  html, body {
    width: 1200px;
    height: 960px;
    overflow: hidden;
    background: var(--backdrop);
    font-family: "Open Sans", Arial, sans-serif;
  }
  .canvas { position: relative; width: 1200px; height: 960px; }

  .card {
    position: absolute;
    left: 320px;
    width: 600px;
    height: 340px;
    box-shadow: 0 3px 8px var(--card-shadow);
  }

  /* Front: contact side */
  .card--front { top: 106px; background: var(--card-blue); color: var(--ink-white); }
  .identity {
    position: absolute;
    right: 345px;
    top: 150px;
    text-align: right;
  }
  .identity__name { font-size: 20px; font-weight: 600; letter-spacing: 0.3px; line-height: 24px; }
  .identity__role { font-size: 15px; font-weight: 400; letter-spacing: 0.3px; line-height: 20px; }
  .divider {
    position: absolute;
    left: 272px;
    top: 142px;
    width: 1.5px;
    height: 62px;
    background: var(--ink-white);
  }
  .contacts {
    position: absolute;
    left: 290px;
    top: 144px;
    list-style: none;
    font-size: 14px;
    font-weight: 400;
    line-height: 19px;
  }
  .contacts li { display: flex; align-items: center; gap: 7px; }
  .contacts svg { width: 12px; height: 12px; fill: var(--ink-white); flex: none; }

  /* Back: brand side */
  .card--back { top: 493px; height: 342px; background: var(--card-white); }
  .brand-name {
    position: absolute;
    left: 0;
    right: 0;
    top: 142px;
    text-align center;
    text-align: center;
    font-size: 56px;
    font-weight: 700;
    color: var(--brand-blue);
    letter-spacing: -0.5px;
    line-height: 66px;
  }
</style>
</head>
<body>
<main class="canvas">
  <section class="card card--front" aria-label="Card front">
    <div class="identity">
      <p class="identity__name">OWEN TALLARD</p>
      <p class="identity__role">CEO/FOUNDER</p>
    </div>
    <div class="divider"></div>
    <ul class="contacts">
      <li>
        <svg viewBox="0 0 24 24" aria-hidden="true"><path d="M6.6 10.8a15.1 15.1 0 0 0 6.6 6.6l2.2-2.2c.3-.3.7-.4 1-.2 1.1.4 2.3.6 3.6.6.6 0 1 .4 1 1V20c0 .6-.4 1-1 1A17 17 0 0 1 3 4c0-.6.4-1 1-1h3.5c.6 0 1 .4 1 1 0 1.3.2 2.5.6 3.6.1.3 0 .7-.2 1z"/></svg>
        <span>0412558903</span>
      </li>
      <li>
        <svg viewBox="0 0 24 24" aria-hidden="true"><path d="M2 5h20v14H2z M3.5 6.5 12 13l8.5-6.5" stroke="#0a84ac" stroke-width="1.6"/></svg>
        <span>owen@linkwayassist.com.au</span>
      </li>
      <li>
        <svg viewBox="0 0 24 24" aria-hidden="true"><circle cx="12" cy="12" r="10"/><path d="M2 12h20M12 2c3 3 3 17 0 20M12 2c-3 3-3 17 0 20" stroke="#0a84ac" stroke-width="1.6" fill="none"/></svg>
        <span>www.linkwayassist.com.au</span>
      </li>
    </ul>
  </section>

  <section class="card card--back" aria-label="Card back">
    <p class="brand-name">Linkway Assist</p>
  </section>
</main>
</body>
</html>
```